Business cards for KORU Real Estate Holdings LLC

We need a cool, original business card design for a company based in the Washington DC metropolitan area. We are a new energetic and passionate Real Estate Investing Company that invests in all types of real estate; commercial, residential, industrial etc.

Our company color is Red since it reflects action, energy and speed; it is assertive confident, energizing, exciting, powerful, passionate and determined. So we would like business card communicate those qualities to the audience.

Our audiences are investors that want to invest with us, real estate sellers, buyers, and tenants who lease from us.

Our logo is attached

```html
<!DOCTYPE html>
<html lang="en">
<head>
<meta charset="utf-8">
<title>KORU Real Estate Holdings LLC – Business Cards</title>
<link href="https://fonts.googleapis.com/css2?family=Arimo:wght@400;700&family=Open+Sans:wght@600&display=swap" rel="stylesheet">
<style>
  :root {
    --backdrop: #ece8e0;
    --card: #ffffff;
    --band: #c9cacc;
    --ink: #1c1c1c;
    --brand-ink: #2a2a2a;
    --red: #d8232a;
    --stripe: #e8545a;
    --shadow: rgba(0,0,0,0.35);
  }
  * { box-sizing: border-box; margin: 0; padding: 0; }
  html, body {
    width: 1200px; height: 960px; overflow: hidden;
    background: var(--backdrop);
    font-family: "Arimo", Arial, sans-serif;
    color: var(--ink);
  }
  .canvas { position: relative; width: 1200px; height: 960px; }

  .card {
    position: absolute;
    width: 720px; height: 400px;
    background: var(--card);
    box-shadow: 3px 4px 8px var(--shadow);
    overflow: hidden;
  }
  .card--front { left: 60px; top: 70px; }
  .card--back  { left: 420px; top: 470px; }

  .stripes {
    position: absolute; height: 12px;
    background: repeating-linear-gradient(to bottom, var(--stripe) 0 1.5px, #fff 1.5px 3px);
  }

  /* front */
  .name-band {
    position: absolute; left: 0; top: 0; width: 100%; height: 56px;
    background: var(--band);
    display: flex; align-items: center; padding-left: 0;
    font-size: 17px;
  }
  .name-band .stripes { position: static; width: 18px; height: 14px; margin: 0 6px 0 0; }
  .name-band .name { margin-right: 28px; }
  .name-band .name em { font-style: normal; color: var(--red); }
  .divider { width: 2px; height: 20px; background: var(--red); margin-right: 18px; }
  .name-band .role { margin-right: 18px; }

  .wordmark {
    position: absolute; display: flex; align-items: center; gap: 14px;
    font-family: "Open Sans", Arial, sans-serif; font-weight: 600;
    color: var(--brand-ink); text-transform: uppercase; line-height: 1.15;
  }
  .wordmark .mark { width: 22px; height: 22px; background: var(--red); flex: none; }
  .card--front .wordmark { left: 300px; top: 150px; font-size: 25px; }
  .card--back .wordmark { left: 150px; top: 140px; font-size: 36px; }

  .address { position: absolute; left: 420px; top: 240px; font-size: 13px; font-weight: 700; }

  .contacts {
    position: absolute; left: 300px; top: 300px;
    display: grid; grid-template-columns: 150px auto; row-gap: 14px; column-gap: 20px;
    font-size: 14px;
  }
  .contact { display: flex; align-items: center; gap: 8px; }
  .contact svg { width: 14px; height: 14px; flex: none; }
</style>
</head>
<body>
<div class="canvas">

  <section class="card card--front">
    <header class="name-band">
      <span class="stripes"></span>
      <span class="name">Name <em>Here</em></span>
      <span class="divider"></span>
      <span class="role">Designation</span>
      <span class="divider"></span>
    </header>

    <div class="wordmark"><span class="mark"></span><span>KORU Real Estate<br>Holdings LLC</span></div>
    <p class="address">Area, state, zipcode, country</p>
    <span class="stripes" style="left:290px; top:262px; width:430px;"></span>
    <span class="stripes" style="left:30px; top:318px; width:140px;"></span>

    <div class="contacts">
      <div class="contact">
        <svg viewBox="0 0 14 14"><rect x="3" y="0.5" width="8" height="13" rx="1.5" fill="var(--red)"/><rect x="4.5" y="2.5" width="5" height="7" fill="#fff"/></svg>
        55 5555 5555
      </div>
      <div class="contact">
        <svg viewBox="0 0 14 14"><rect x="1" y="3" width="12" height="3" fill="var(--ink)"/><polygon points="3,6 11,6 13,13 1,13" fill="var(--ink)"/></svg>
        info@koruholdings.com
      </div>
      <div class="contact">
        <svg viewBox="0 0 14 14"><path d="M1 4h12v2H1z M3 6h8l2 7H1z" fill="var(--ink)"/><circle cx="7" cy="9.5" r="1.6" fill="#fff"/></svg>
        44 4444 4444
      </div>
      <div class="contact">
        <svg viewBox="0 0 14 14" fill="none" stroke="var(--ink)" stroke-width="1"><circle cx="7" cy="7" r="6"/><ellipse cx="7" cy="7" rx="2.6" ry="6"/><path d="M1 7h12M2 4h10M2 10h10"/></svg>
        www.koruholdings.com
      </div>
    </div>
  </section>

  <section class="card card--back">
    <div class="wordmark"><span class="mark"></span><span>KORU Real Estate<br>Holdings LLC</span></div>
    <span class="stripes" style="left:0; top:300px; width:140px;"></span>
    <span class="stripes" style="left:260px; top:290px; width:460px;"></span>
  </section>

</div>
</body>
</html>
```